Quarrybend Marble & Tile Needs a Business Card

Attached you will find your logo, my photo and design guidelines for a new business card. The final design will need two separate files to create an embossed card. The cards will be printed by www.plinkprint.com (Instructions below)
Format is the Plink SQUARE card
Quarrybend Marble And Tile is a brick and mortar, retail stone and tile shop.
One the front:
Quarrybend Marble And Tile
Dorian Fesslock
Owner
24807 Hollis Verdant Blvd
Suite P & R
Charlotte, NC 28193
Cell: 704-583-7142
Web: www.QuarrybendMarbleAndTile.com
(Make each word of the domain a different or alternating color)
On the back;
Something that shows beautiful colorful tile
Follow the design guide closely please. For more information see this page that describes creating the spot gloss file: https://www.plinkprint.com/us/business-cards/design-guidelines-spot-gloss
The logo is what we would like to have raised spot glossed.
Format is the Plink SQUARE card. See attahced guidlines.

```html
<!DOCTYPE html>
<html lang="en">
<head>
<meta charset="utf-8">
<title>Quarrybend Marble &amp; Tile — Business Card</title>
<link rel="stylesheet" href="https://fonts.googleapis.com/css2?family=Mulish:wght@400;600;700&family=Cormorant+Garamond:ital,wght@0,600;1,500&display=swap">
<style>
  :root {
    --backdrop: #2f2f30;
    --card-stock: #ecebe7;
    --ink-charcoal: #3a3a3b;
    --ink-grey: #4a4a4c;
    --ink-navy: #1f2e50;
    --ink-gold: #b38b48;
    --mark-grey: #dcdbd7;
    --tile-navy: #2c3a55;
    --tile-slate: #5d6270;
    --tile-stone: #9a9a9c;
    --tile-white: #d9d9d8;
    --tile-cream: #cfc6b4;
  }
  * { margin: 0; padding: 0; box-sizing: border-box; }
  html, body {
    width: 1200px;
    height: 1200px;
    overflow: hidden;
    background: var(--backdrop);
  }
  .canvas {
    position: relative;
    width: 1200px;
    height: 1200px;
  }
  .card {
    position: absolute;
    top: 299px;
    width: 555px;
    height: 622px;
  }
  .card-front {
    left: 27px;
    background: var(--card-stock);
    font-family: "Mulish", sans-serif;
    color: var(--ink-grey);
    text-align: center;
  }
  .card-back {
    left: 618px;
    width: 554px;
    background:
      linear-gradient(135deg,
        var(--tile-slate) 0%,
        var(--tile-navy) 18%,
        var(--tile-white) 36%,
        var(--tile-cream) 48%,
        var(--tile-navy) 60%,
        var(--tile-stone) 76%,
        var(--tile-white) 100%);
  }
  .brand-square {
    position: absolute;
    left: 50%;
    top: 372px;
    top: 66px;
    width: 70px;
    height: 70px;
    margin-left: -35px;
    background: var(--mark-grey);
  }
  .brand-name {
    position: absolute;
    left: 0;
    right: 0;
    top: 176px;
    font-family: "Cormorant Garamond", serif;
    font-weight: 600;
    color: var(--ink-charcoal);
  }
  .brand-name .brand-main {
    display: block;
    font-size: 62px;
    line-height: 64px;
    letter-spacing: 1px;
  }
  .brand-name .brand-sub {
    display: block;
    margin-top: 6px;
    font-size: 26px;
    line-height: 30px;
    letter-spacing: 5px;
    text-transform: uppercase;
  }
  .owner-name {
    position: absolute;
    left: 0; right: 0;
    top: 343px;
    font-weight: 600;
    font-size: 22px;
    letter-spacing: 3px;
    color: var(--ink-navy);
    text-transform: uppercase;
  }
  .owner-title {
    position: absolute;
    left: 0; right: 0;
    top: 374px;
    font-family: "Cormorant Garamond", serif;
    font-style: italic;
    font-weight: 500;
    font-size: 19px;
    color: var(--ink-grey);
  }
  .address {
    position: absolute;
    left: 0; right: 0;
    top: 406px;
    font-size: 19px;
    line-height: 24.5px;
    font-style: normal;
  }
  .divider {
    position: absolute;
    left: 167px;
    width: 220px;
    top: 494px;
    height: 2px;
    background: var(--ink-gold);
  }
  .contact-line {
    position: absolute;
    left: 0; right: 0;
    font-size: 19px;
  }
  .contact-line .label { font-weight: 700; }
  .cell { top: 510px; }
  .web { top: 552px; }
  .web .word-gold { color: var(--ink-gold); }
  .web .word-navy { color: var(--ink-navy); }
</style>
</head>
<body>
<main class="canvas">
  <section class="card card-front">
    <div class="brand-square"></div>
    <h1 class="brand-name"><span class="brand-main">Quarrybend</span><span class="brand-sub">Marble &amp; Tile</span></h1>
    <p class="owner-name">Dorian Fesslock</p>
    <p class="owner-title">Owner</p>
    <address class="address">
      24807 Hollis Verdant Blvd<br>
      Suite P &amp; R<br>
      Charlotte, NC 28193
    </address>
    <div class="divider"></div>
    <p class="contact-line cell"><span class="label">Cell:</span> 704-583-7142</p>
    <p class="contact-line web"><span class="label">Web:</span> www.<span class="word-gold">Quarrybend</span><span class="word-navy">Marble</span><span class="word-gold">And</span><span class="word-navy">Tile</span>.com</p>
  </section>
  <section class="card card-back" role="img" aria-label="Mosaic of veined marble and patterned tiles in navy, grey, white and cream laid on a diagonal"></section>
</main>
</body>
</html>
```